Web design project for exciting Australian start-up

Background
We are looking for a creative and talented web design artist to work alongside our market leading web developer.
• You will be required to create a modern and clean design theme for our website, incorporating selected rustic colour scheme elements for our exciting Australian start-up to operate within the coffee industry.
reoccurring work to be expected to flow to the successful designer.
Requirements
• c. 5 - 10 page website
• Landing page
• Log in/ out
• 404 template
• Typography is emphasised
• Please use either a) typemarrow.com, b) free web fonts, c) brindle fonts
• All design elements in vector format
• Preferably with icons for each header title(i.e. about us, how it works etc) but designer have free reign over how the site looks, so might not be applicable
• All pages to be responsive
• Down to eSlab resolution

High level visual design brief attached - additional pages to be worked from base design.

Design inspiration
• We would like to use design elements from the following sources:
http://www.zandrix.com/halcyon/ (Functionality)
Colour scheme refer to logo and complementary style guide

```html
<!DOCTYPE html>
<html lang="en">
<head>
<meta charset="utf-8">
<title>Brewline — Coffee Marketplace</title>
<link href="https://fonts.googleapis.com/css2?family=Open+Sans:wght@400;700&family=Zilla+Slab:wght@300;400;500&display=swap" rel="stylesheet">
<style>
  :root {
    --orange: #fd9b33;
    --red: #e8383d;
    --ink: #222222;
    --text-muted: #555555;
    --nav-active: #f3f3f3;
    --divider: #ececec;
    --footer-bg: #e8e8e8;
    --footer-text: #5a5a5a;
    --bar-bg: #4b4b4b;
    --white: #ffffff;
  }
  * { box-sizing: border-box; margin: 0; padding: 0; }
  html, body { width: 1200px; height: 950px; overflow: hidden; background: var(--white); }
  body { font-family: "Open Sans", Arial, sans-serif; color: var(--ink); }
  .page { position: relative; width: 1200px; height: 950px; }

  /* Header */
  .site-header { position: absolute; left: 0; top: 0; width: 1200px; height: 107px; background: var(--white); }
  .brand { position: absolute; left: 161px; top: 30px; display: flex; align-items: center; gap: 10px; }
  .brand-mark { width: 40px; height: 40px; border-radius: 50%; background: var(--orange); }
  .brand-name { font-family: "Zilla Slab", Georgia, serif; font-weight: 500; font-size: 32px; letter-spacing: 2px; color: var(--ink); text-transform: uppercase; }

  .main-nav { position: absolute; left: 560px; top: 0; height: 107px; display: flex; border-right: 1px solid var(--divider); }
  .nav-item { height: 107px; display: flex; flex-direction: column; align-items: center; padding-top: 29px; border-left: 1px solid var(--divider); font-size: 12px; color: #333; text-transform: uppercase; text-decoration: none; }
  .nav-item svg { width: 20px; height: 20px; margin-bottom: 6px; }
  .nav-item.is-active { background: var(--nav-active); }
  .nav-about { width: 94px; }
  .nav-how { width: 135px; }
  .nav-faq { width: 66px; }

  .auth { position: absolute; top: 38px; left: 878px; display: flex; gap: 9px; }
  .btn { display: inline-flex; align-items: center; justify-content: center; height: 31px; width: 76px; font-family: "Zilla Slab", Georgia, serif; font-size: 15px; color: var(--white); border-radius: 2px; text-decoration: none; }
  .btn-login { background: var(--orange); }
  .btn-signup { background: var(--red); }

  /* Hero */
  .hero { position: absolute; left: 0; top: 107px; width: 1200px; height: 543px; overflow: hidden; }
  .hero-media { position: absolute; inset: 0;
    background:
      radial-gradient(ellipse 420px 120px at 600px 520px, #8a4f22 0%, #4a2510 55%, transparent 100%),
      radial-gradient(ellipse 260px 300px at 520px 120px, #b8692c 0%, #6a3512 45%, transparent 85%),
      #080402; }
  .hero-copy { position: absolute; left: 0; width: 1200px; top: 209px; text-align: center; color: var(--white); }
  .hero-kicker { font-size: 22px; font-weight: 400; line-height: 30px; }
  .hero-title { font-size: 36px; font-weight: 700; line-height: 44px; letter-spacing: .5px; margin-top: 2px; }
  .btn-video { position: absolute; left: 519px; top: 302px; width: 162px; height: 45px; background: var(--orange); color: var(--white); font-family: "Zilla Slab", Georgia, serif; font-size: 19px; display: flex; align-items: center; justify-content: center; text-decoration: none; }
  .slider-arrow { position: absolute; top: 239px; width: 56px; height: 56px; }
  .slider-prev { left: 161px; }
  .slider-next { left: 982px; }

  /* Footer */
  .site-footer { position: absolute; left: 0; top: 650px; width: 1200px; height: 236px; background: var(--footer-bg); }
  .footer-col { position: absolute; top: 50px; }
  .footer-col h3 { font-family: "Zilla Slab", Georgia, serif; font-weight: 400; font-size: 19px; color: var(--ink); letter-spacing: .5px; text-transform: uppercase; margin-bottom: 12px; }
  .footer-col ul { list-style: none; }
  .footer-col li { font-family: "Zilla Slab", Georgia, serif; font-weight: 300; font-size: 15px; color: var(--footer-text); line-height: 31px; }
  .col-info { left: 295px; }
  .col-who { left: 541px; }
  .col-who ul { padding-left: 3px; }
  .col-join { left: 797px; }
  .col-join ul { padding-left: 3px; }
  .social li { display: flex; align-items: center; }
  .social-label { width: 76px; }
  .social-dot { width: 10px; height: 10px; background: #666; border-radius: 2px; }

  .bottom-bar { position: absolute; left: 0; top: 886px; width: 1200px; height: 64px; background: var(--bar-bg); }
  .bottom-rule { position: absolute; left: 161px; top: 5px; width: 877px; height: 1px; background: #6a6a6a; }
  .copyright { position: absolute; left: 0; width: 1200px; top: 22px; text-align: center; font-family: "Zilla Slab", Georgia, serif; font-size: 15px; color: var(--white); }
</style>
</head>
<body>
<div class="page">
  <header class="site-header">
    <div class="brand">
      <span class="brand-mark"></span>
      <span class="brand-name">Brewline</span>
    </div>
    <nav class="main-nav">
      <a class="nav-item nav-about is-active" href="#">
        <svg viewBox="0 0 20 20" fill="none" stroke="#fd9b33" stroke-width="1.3"><path d="M3 10 L10 3 L17 10"/><path d="M5 8.5 V17 H15 V8.5"/><path d="M8.5 17 V12 H11.5 V17"/></svg>
        About us
      </a>
      <a class="nav-item nav-how" href="#">
        <svg viewBox="0 0 20 20" fill="none" stroke="#666" stroke-width="1.3"><circle cx="8" cy="7" r="3"/><path d="M2.5 17 C3 12.5 13 12.5 13.5 17"/><rect x="12" y="2" width="6" height="5"/></svg>
        How it works
      </a>
      <a class="nav-item nav-faq" href="#">
        <svg viewBox="0 0 20 20" fill="none" stroke="#666" stroke-width="1.3"><rect x="4" y="6" width="4" height="12"/><rect x="11" y="2" width="4" height="16"/><path d="M11 6 H13 M11 10 H13 M11 14 H13"/></svg>
        FAQ
      </a>
    </nav>
    <div class="auth">
      <a class="btn btn-login" href="#">Login</a>
      <a class="btn btn-signup" href="#">Sign up</a>
    </div>
  </header>

  <section class="hero">
    <div class="hero-media" role="img" aria-label="Photograph of a pile of roasted coffee beans with warm smoke rising against a dark background"></div>
    <div class="hero-copy">
      <p class="hero-kicker">AUSTRALIA FIRST ONLINE</p>
      <h1 class="hero-title">COFFEE MARKETPLACE</h1>
    </div>
    <a class="btn-video" href="#">Watch Video</a>
    <svg class="slider-arrow slider-prev" viewBox="0 0 56 56" fill="none" stroke="#fff"><circle cx="28" cy="28" r="26.5" stroke-width="2.5"/><path d="M31 21 L24 28 L31 35" stroke-width="2"/></svg>
    <svg class="slider-arrow slider-next" viewBox="0 0 56 56" fill="none" stroke="#fff"><circle cx="28" cy="28" r="26.5" stroke-width="2.5"/><path d="M25 21 L32 28 L25 35" stroke-width="2"/></svg>
  </section>

  <footer class="site-footer">
    <div class="footer-col col-info">
      <h3>Helpful Info</h3>
      <ul>
        <li>About Us</li>
        <li>Media Enquiries</li>
        <li>Terms &amp; Conditions</li>
        <li>Privacy Policy</li>
      </ul>
    </div>
    <div class="footer-col col-who">
      <h3>Who We Are</h3>
      <ul>
        <li>How it works</li>
        <li>FAQ</li>
        <li>Contact us</li>
      </ul>
    </div>
    <div class="footer-col col-join">
      <h3>Join Us On</h3>
      <ul class="social">
        <li><span class="social-label">Friendspace</span><span class="social-dot"></span></li>
        <li><span class="social-label">Chirpline</span><span class="social-dot"></span></li>
        <li><span class="social-label">Workchain</span><span class="social-dot"></span></li>
        <li><span class="social-label">ClipStream</span><span class="social-dot"></span></li>
      </ul>
    </div>
  </footer>

  <div class="bottom-bar">
    <div class="bottom-rule"></div>
    <p class="copyright">Copyright © 2014 Brewline</p>
  </div>
</div>
</body>
</html>
```